Fitness Equipment Repair Business Needs a Catchy New Business Card

We have an existing business card, however, it is quite plain and boring. We are expanding primarily in the commercial area (gyms, studios, apartment complexes etc). The business card will serve as eye candy to those managers/owners that can't be met for a face to face.
Originally I was planning for a brochure as well, but all of our information is better summarized on our website. (brightloopservice.ca).
I would like the card to match the colour scheme of the website and utilize the logo. It should have a professional clean feel to it, however, a little colouring outside the lines wouldn't hurt.
The example card is for my service technician (Colin Marsh). If possible I would like to be able to edit the text to use for more than one person.

Industry/Entity Type

Appliance Repair

Contact Information for Business Card

Clean, crisp and professional but needs to be eye catching. Preferably using the black, white and red colour scheme matching the website. Double sided would be nice, but is not necessary.

Colors
ec1f27
ffffff
000000

Requirements
Must have
• Must be able to edit name, phone number and title to use for multiple people. Must show the company website (brightloopservice.ca).

```html
<!DOCTYPE html>
<html lang="en">
<head>
<meta charset="utf-8">
<title>Bright Loop Service – Business Card</title>
<link rel="stylesheet" href="https://fonts.googleapis.com/css2?family=Cinzel:wght@500;700&family=PT+Sans:wght@400&display=swap">
<style>
  :root {
    --red: #ec1f27;
    --black: #000000;
    --white: #ffffff;
    --ink: #4a4a4a;
    --stage: #e6e3df;
    --display: "Cinzel", serif;
    --body: "PT Sans", sans-serif;
  }
  * { margin: 0; padding: 0; box-sizing: border-box; }
  html, body { width: 1200px; height: 987px; overflow: hidden; }
  body { background: var(--stage); position: relative; font-family: var(--body); }

  .card { position: absolute; left: 293px; width: 615px; height: 351px; box-shadow: 0 2px 6px rgba(0,0,0,.25); overflow: hidden; }
  .card--front { top: 130px; background: var(--white); }
  .card--back { top: 506px; background: var(--red); }

  /* front */
  .brand-panel { position: absolute; left: 0; top: 0; width: 332px; height: 100%; background: var(--black); border-right: 4px solid var(--red); }
  .brand-panel .figure { position: absolute; left: 30px; top: 112px; width: 72px; height: 116px; border-radius: 36px 36px 6px 6px; background: radial-gradient(circle at 50% 40%, #3a3a3a, #111 75%); }
  .brand-panel .company { position: absolute; left: 108px; top: 156px; font-family: var(--display); font-weight: 700; font-size: 18px; color: var(--white); white-space: nowrap; }

  .details { position: absolute; left: 366px; top: 68px; }
  .name { font-family: var(--display); font-weight: 700; font-size: 26px; color: var(--red); letter-spacing: .5px; line-height: 1; }
  .title { font-family: var(--display); font-weight: 500; font-size: 18px; color: var(--ink); margin-top: 5px; }
  .address { font-size: 15px; color: var(--ink); line-height: 23px; margin-top: 12px; }
  .contacts { list-style: none; margin-top: 12px; }
  .contacts li { display: flex; align-items: center; font-size: 15px; color: var(--ink); height: 23.5px; }
  .contacts svg { width: 14px; height: 14px; margin-right: 9px; fill: var(--red); flex: none; }
  .contacts small { font-size: 12px; }

  /* back */
  .hero { position: absolute; left: 14px; top: 10px; width: 228px; height: 326px; border-radius: 100px 100px 10px 10px; background: radial-gradient(ellipse at 45% 40%, #f6595e, var(--red) 72%); }
  .back-company { position: absolute; left: 293px; top: 264px; font-family: var(--display); font-weight: 700; font-size: 24px; color: var(--white); white-space: nowrap; }
  .back-web { position: absolute; left: 293px; top: 297px; font-size: 15px; letter-spacing: 3.4px; color: var(--white); white-space: nowrap; }
</style>
</head>
<body>

<section class="card card--front">
  <div class="brand-panel">
    <div class="figure" role="img" aria-label="Company logo: line illustration of a technician in a hard hat holding a wrench"></div>
    <span class="company">Bright Loop Service</span>
  </div>
  <div class="details">
    <h1 class="name">Colin Marsh</h1>
    <p class="title">Service technician</p>
    <p class="address">118 Harlow Road NW<br>Edmonton AB T5K 2P4</p>
    <ul class="contacts">
      <li><svg viewBox="0 0 24 24"><path d="M6.6 10.8a15.1 15.1 0 0 0 6.6 6.6l2.2-2.2a1 1 0 0 1 1-.25 11.4 11.4 0 0 0 3.6.57 1 1 0 0 1 1 1V20a1 1 0 0 1-1 1A17 17 0 0 1 3 4a1 1 0 0 1 1-1h3.5a1 1 0 0 1 1 1c0 1.25.2 2.45.57 3.6a1 1 0 0 1-.25 1z"/></svg>555-014-2208<small>(Personal)</small></li>
      <li><svg viewBox="0 0 24 24"><path d="M6.6 10.8a15.1 15.1 0 0 0 6.6 6.6l2.2-2.2a1 1 0 0 1 1-.25 11.4 11.4 0 0 0 3.6.57 1 1 0 0 1 1 1V20a1 1 0 0 1-1 1A17 17 0 0 1 3 4a1 1 0 0 1 1-1h3.5a1 1 0 0 1 1 1c0 1.25.2 2.45.57 3.6a1 1 0 0 1-.25 1z"/></svg>555-019-6631<small>(Service Line)</small></li>
      <li><svg viewBox="0 0 24 24"><path d="M2 5h20v14H2z"/><path d="M2 5l10 8 10-8" stroke="#fff" stroke-width="1.6" fill="none"/></svg>hello@brightloopservice.ca</li>
      <li><svg viewBox="0 0 24 24"><circle cx="12" cy="12" r="10"/><path d="M7 9c2-1 3 1 5 0s2-3 4-2M8 16c2 1 4-1 6 1" stroke="#fff" stroke-width="1.6" fill="none"/></svg>brightloopservice.ca</li>
    </ul>
  </div>
</section>

<section class="card card--back">
  <div class="hero" role="img" aria-label="Company logo: large line illustration of a technician in a hard hat holding a wrench"></div>
  <span class="back-company">Bright Loop Service</span>
  <span class="back-web">www.brightloopservice.ca</span>
</section>

</body>
</html>
```